New word press website site design

We provide email marketing to aircraft brokers and dealers to assist in finding buyers for their aircraft.

Our target market to purchase our broadcasts are the aircraft sellers – NOT the buyers.

Our target market when sending the email broadcast, are the buyers (end users).

The website should target brokers and our email database targets the buyers.

We do not buy or sell aircraft as a company. We provide email marketing solutions to connect buyers and sellers of aircraft.

Our other site is planelantern.com and will be redesigned soon. Please use it as a reference as far as general scope but they layout can be completely different and should include helicopters only as far as imagery. The colors should be similar as the logos are similar, however we do NOT want both sites to be identical in use of primary color

Plenty of images and sample broadcasts attached to use as needed throughout the site.

Headlines listed below with some text copy.

In the event that we need to add more text, please use standard greek text as a place holder for the purposes of the mockup design.

Need to have a “SUBSCRIBE” button to join our mailing list.

Possible Headlines:

Exclusively Showcasing Rotor Wing Aircraft to the Global Marketplace

Showcasing Pre-Owned Helicopters Available For Sale, Lease, Trade, or Wanted for Acquisition.

Mobile-optimized Email Campaigns that Render Correctly Across all Devices

Targeted worldwide recipients that currently own, operate, or have an interest in rotor wing aircraft

STRONGEST Rotor Wing Database in the Industry

Text/Copy:

HOME
Rotorbay Vista is one of most powerful marketing tools in the industry to utilize in reaching targeted buyers of pre-owned helicopters. Rotorbay Vista provides the rotor wing aircraft market with a fast, effective, and affordable email broadcast solution to utilize in the marketing of Helicopters for sale.

Developed Exclusively to Showcase Rotor Wing Aircraft to the Global marketplace, Rotorbay Vista is a powerful tool designed to maximize leads and accelerate the sales process by providing the ability to reach a global network of Helicopter buyers in a matter of seconds.

DATABASE:

While Rotorbay Vista is delivered to all known broker/dealers, our primary focus is in reaching end users. Our opt-in/opt-out recipient database is updated daily and developed specifically to deliver the latest details on helicopters available for sale or lease to the inboxes of a global network of Helicopter buyers and sellers.

· Helicopter Owners

· Helicopter Operators

· Helicopter Charter Services

· Helicopter Management Companies

· Corporate/Municipal Flight Departments

· Helicopter Pilots

· Senior Aviation Executives

· Wealth Management Firms

· High Net Worth Individuals

· Helicopter Broker/Dealers

Helicopter Tour/Travel Firms

· Off Shore Oil & Gas Production Firms

· Municipalities/Media/Medevac Firms

Our recipient database is continuously updated and developed specifically to reach buyers and sellers of Helicopters. This ensures that your Helicopter will be showcased to the right people. Rotorbay Vista does not broadcast non-rotor wing aircraft and focuses exclusively on the Global Helicopter Market.

Broadcast Design:

Rotorbay Vista broadcast ads are custom designed for you by incorporating your corporate image and branding. Because you have worked hard in developing your corporate image, we strive to maintain it while designing an ad that will showcase your Helicopter to its best advantage. Rotorbay Vista utilizes Mobile-optimized Email Campaigns with Responsive Coding to render correctly across all devices

Once you have approved the design, we schedule the broadcast to be sent on the available date and time you request. The broadcast will link to your website and the results can be immediate. All email leads and replies will go to the email address that you provided.

Pricing:
Create a place holder for 3 Different Broadcast Packages

-Broadcast Package A
-Broadcast Package B
-Broadcast Package C

Target Market(s)

The target market is any person or company that has aircraft for sale. We work with brokers, dealers, and owners to assist in finding buyers for their aircraft using email marketing campaigns (Showcase broadcasts).

Industry/Entity Type

Aviation

Colors
0255a3
00a990

Requirements
Nice to have
• Samples of helicopter for sale broadcast ads in /image gallery/slider

```html
<!DOCTYPE html>
<html lang="en">
<head>
<meta charset="UTF-8">
<title>Rotorbay Vista — Skyframe Media Inc</title>
<link rel="stylesheet" href="https://fonts.googleapis.com/css2?family=Montserrat:wght@300;400;500;600;700&display=swap">
<style>
  :root {
    --black: #000000;
    --ink: #ffffff;
    --rule-blue: #1f4f7d;
    --navy: #163f66;
    --navy-button: #1a3e66;
    --copper: #d2914f;
    --copper-text: #d9914a;
    --frame: #c98a4c;
  }
  * { margin: 0; padding: 0; box-sizing: border-box; }
  html, body {
    width: 1200px;
    height: 4327px;
    overflow: hidden;
    background: var(--black);
    color: var(--ink);
    font-family: "Montserrat", Arial, sans-serif;
  }
  .page { position: relative; width: 1200px; height: 4327px; }
  .rule { height: 12px; background: var(--rule-blue); }
  .rule.thin { height: 9px; }

  /* Header */
  .site-header { height: 276px; display: flex; flex-direction: column; align-items: center; justify-content: flex-end; padding-bottom: 20px; }
  .brand { font-weight: 700; font-size: 30px; letter-spacing: 1px; text-transform: uppercase; display: flex; align-items: center; gap: 16px; }
  .brand-dot { width: 18px; height: 18px; border-radius: 50%; background: var(--ink); }

  /* Hero */
  .hero { position: relative; height: 823px; }
  .hero-photo {
    position: absolute; inset: 0;
    background: linear-gradient(180deg, #1d3247 0%, #6f8fb3 25%, #a9c0d8 42%, #4a4e4d 62%, #2b2d2c 74%, #050505 92%, #000 100%);
  }
  .hero-title {
    position: absolute; left: 0; right: 0; top: 940px; top: 652px;
    text-align: center; font-weight: 700; font-size: 45px; line-height: 58px;
  }

  /* Welcome */
  .welcome { height: 620px; text-align: center; padding-top: 110px; }
  .section-title { font-weight: 700; font-size: 54px; letter-spacing: 1px; }
  .welcome p { width: 990px; margin: 28px auto 0; font-size: 27px; font-weight: 400; line-height: 55px; }
  .actions { display: flex; justify-content: center; gap: 12px; margin-top: 34px; }
  .btn {
    display: inline-flex; align-items: center; justify-content: center;
    height: 69px; width: 242px; border-radius: 35px;
    font-size: 25px; font-weight: 500; color: var(--ink); text-transform: uppercase;
  }
  .btn-copper { background: var(--copper); }
  .btn-navy { background: var(--navy-button); }

  /* Database */
  .database { height: 1174px; padding: 98px 52px 0; }
  .database .section-title { text-align: left; }
  .database p { margin-top: 22px; width: 1000px; font-size: 26px; line-height: 49px; }
  .audience { display: grid; grid-template-columns: 591px 1fr; margin-top: 20px; padding-left: 4px; }
  .audience ul { list-style: none; }
  .audience li { font-size: 26px; line-height: 49px; display: flex; align-items: center; gap: 20px; }
  .audience li::before { content: ""; width: 16px; height: 16px; border: 3px solid var(--ink); border-radius: 50%; flex: none; }
  .gallery { display: flex; gap: 46px; margin-top: 62px; }
  .gallery-photo { width: 516px; height: 332px; border: 6px solid var(--frame); }
  .photo-day { background: linear-gradient(180deg, #3a86d2 0%, #7fb6ea 55%, #3f6a2a 80%, #2f4f21 100%); }
  .photo-night { background: radial-gradient(ellipse at 50% 75%, #8b7a62 0%, #2c2a27 35%, #0b0b0b 75%); }

  /* Pricing */
  .pricing { height: 822px; padding-top: 80px; }
  .pricing .section-title { text-align: center; font-weight: 600; }
  .plans { display: flex; justify-content: center; gap: 26px; margin-top: 58px; }
  .plan { position: relative; width: 341px; height: 458px; border: 3px solid var(--ink); padding: 44px 0 0 42px; }
  .plan-kind { color: var(--copper-text); font-size: 29px; font-weight: 500; }
  .plan-name { font-size: 36px; font-weight: 500; margin-top: 8px; }
  .plan ul { list-style: none; margin-top: 22px; }
  .plan li { font-size: 27px; line-height: 55px; display: flex; align-items: center; gap: 22px; }
  .plan li::before { content: ""; width: 20px; height: 20px; border-radius: 50%; flex: none; background: radial-gradient(circle, var(--ink) 0 4px, transparent 5px); border: 3px solid var(--ink); }
  .plan .btn { position: absolute; left: 50%; bottom: -36px; transform: translateX(-50%); width: 218px; }

  /* Footer */
  .site-footer { height: 577px; background: var(--navy); text-align: center; padding-top: 102px; }
  .social { display: flex; justify-content: center; gap: 9px; }
  .social span { width: 87px; height: 87px; border: 3px solid var(--ink); border-radius: 50%; }
  .site-footer .brand { justify-content: center; margin-top: 100px; }
  .copyright { font-size: 24px; margin-top: 110px; }
</style>
</head>
<body>
<div class="page">
  <div class="rule"></div>

  <header class="site-header">
    <div class="brand"><span class="brand-dot"></span>Skyframe Media Inc</div>
  </header>

  <section class="hero">
    <div class="hero-photo" role="img" aria-label="Black twin-engine helicopter parked on a helipad at an airfield under a blue sky"></div>
    <h1 class="hero-title">Exclusively Showcasing Rotor Wing Aircraft<br>to the Global Marketplace</h1>
  </section>

  <div class="rule"></div>

  <section class="welcome">
    <h2 class="section-title">WELCOME</h2>
    <p>Rotorbay Vista is one of most powerful marketing tools in the industry to utilize in reaching targeted buyers of pre-owned helicopters. Rotorbay Vista provides the rotor wing aircraft market with a fast, effective, and affordable email broadcast solution to utilize in the marketing of Helicopters for sale.</p>
    <div class="actions">
      <a class="btn btn-copper">Read More</a>
      <a class="btn btn-navy">Subscribe</a>
    </div>
  </section>

  <div class="rule thin"></div>

  <section class="database">
    <h2 class="section-title">DATABASE</h2>
    <p>While Rotorbay Vista is delivered to all known broker/dealers, our primary focus is in reaching end users. Our opt-in/opt-out recipient database is updated daily and developed specifically ..</p>
    <div class="audience">
      <ul>
        <li>Helicopter Owners</li>
        <li>Helicopter Operators</li>
        <li>Helicopter Charter Services</li>
        <li>Helicopter Management Companies</li>
        <li>Corporate/Municipal Flight Departments</li>
        <li>Helicopter Pilots</li>
        <li>Senior Aviation Executives</li>
      </ul>
      <ul>
        <li>Wealth Management Firms</li>
        <li>High Net Worth Individuals</li>
        <li>Helicopter Broker/Dealers</li>
        <li>Helicopter Tour/Travel Firms</li>
        <li>Off Shore Oil &amp; Gas Production Firms</li>
        <li>Municipalities/Media/Medevac Firms</li>
      </ul>
    </div>
    <div class="gallery">
      <div class="gallery-photo photo-day" role="img" aria-label="Dark helicopter facing forward on grass under a bright blue sky"></div>
      <div class="gallery-photo photo-night" role="img" aria-label="White helicopter with landing lights on at night on a lit helipad"></div>
    </div>
  </section>

  <div class="rule thin"></div>

  <section class="pricing">
    <h2 class="section-title">Pricing</h2>
    <div class="plans">
      <article class="plan">
        <div class="plan-kind">Broadcast</div>
        <h3 class="plan-name">Package-A</h3>
        <ul><li>Magni dolores</li><li>Eos quiratione</li><li>Quis nostrum</li><li>Exercitationem</li></ul>
        <a class="btn btn-copper">Buy Now</a>
      </article>
      <article class="plan">
        <div class="plan-kind">Broadcast</div>
        <h3 class="plan-name">Package-B</h3>
        <ul><li>Magni dolores</li><li>Eos quiratione</li><li>Quis nostrum</li><li>Exercitationem</li></ul>
        <a class="btn btn-copper">Buy Now</a>
      </article>
      <article class="plan">
        <div class="plan-kind">Broadcast</div>
        <h3 class="plan-name">Package-C</h3>
        <ul><li>Magni dolores</li><li>Eos quiratione</li><li>Quis nostrum</li><li>Exercitationem</li></ul>
        <a class="btn btn-copper">Buy Now</a>
      </article>
    </div>
  </section>

  <footer class="site-footer">
    <div class="social" aria-label="Social links">
      <span></span><span></span><span></span><span></span><span></span>
    </div>
    <div class="brand"><span class="brand-dot"></span>Skyframe Media Inc</div>
    <p class="copyright">Copyrights © 2018, Skyframe Media Inc.All rights reserved.</p>
  </footer>
</div>
</body>
</html>
```